Verodex business card

Business card for sustainable investment company called "Verodex". Verodex is an exchange platform selling carbon credits between buyers and sellers. Carbon Credits are an environmental commodity for reducing global carbon emissions.

the card should obviously have our logo and the theme should be sustainability/environment mixed with a trading platform.

Contact Information for Business Card

Logo, Name, Title, Phone, Email

Colors
0054AA
0677BA
7BADD7
CADEEF
E8F1F8
0094D4
00A9DD
6FCCEA
C7EBF8
E9F6FB
00AB8E
00BBA5
67D7C9
C6EFE9
E9F9F6
59FF00
82FF00
B8FF75
E3FFCB
F4FFEA

```html
<!DOCTYPE html>
<html lang="en">
<head>
<meta charset="UTF-8">
<title>Verodex business card</title>
<link rel="stylesheet" href="https://fonts.googleapis.com/css2?family=Open+Sans:wght@400;600;700&display=swap">
<style>
  :root {
    --backdrop: #4a4a4a;
    --paper: #fdfdf3;
    --navy: #13294f;
    --ink: #1a1a1a;
    --brand-blue: #4a7fcb;
    --band-start: #6fccea;
    --band-end: #4a7fcb;
    --rule: #1f3468;
  }
  * { box-sizing: border-box; margin: 0; padding: 0; }
  html, body { width: 1200px; height: 780px; overflow: hidden; }
  body {
    background: var(--backdrop);
    font-family: "Open Sans", Arial, sans-serif;
    position: relative;
  }
  .card {
    position: absolute;
    top: 230px;
    width: 560px;
    height: 320px;
    background: var(--paper);
    box-shadow: 0 6px 18px rgba(0,0,0,.35);
    overflow: hidden;
  }
  .card--front { left: 30px; }
  .card--back { left: 610px; }

  .brand {
    position: absolute;
    display: flex;
    align-items: center;
    color: var(--navy);
    font-weight: 700;
    letter-spacing: .04em;
    text-transform: uppercase;
  }
  .brand__square { background: var(--brand-blue); flex: none; }

  .card--front .brand { left: 0; right: 0; top: 0; bottom: 0; justify-content: center; font-size: 64px; gap: 22px; }
  .card--front .brand__square { width: 58px; height: 58px; }

  .card--back .brand { left: 34px; top: 128px; font-size: 34px; gap: 12px; }
  .card--back .brand__square { width: 34px; height: 34px; }

  .divider {
    position: absolute;
    left: 318px; top: 42px;
    width: 1.5px; height: 186px;
    background: var(--rule);
  }
  .contact { position: absolute; left: 342px; top: 48px; }
  .contact__name { color: var(--brand-blue); font-weight: 700; font-size: 25px; line-height: 1.1; }
  .contact__title { color: var(--ink); font-weight: 600; font-size: 14px; margin-top: 2px; }
  .contact__list { list-style: none; margin-top: 18px; }
  .contact__item { display: flex; align-items: center; gap: 9px; font-size: 14px; color: var(--ink); line-height: 1.55; }
  .contact__item svg { width: 13px; height: 13px; flex: none; }

  .address-band {
    position: absolute;
    left: 0; bottom: 34px;
    width: 100%; height: 40px;
    display: flex;
  }
  .address-band__stripe {
    flex: 1;
    background: linear-gradient(90deg, var(--band-start), var(--band-end));
    color: #fff;
    font-size: 15px;
    display: flex; align-items: center;
    padding-left: 96px;
  }
  .address-band__tab { width: 62px; background: var(--navy); }
</style>
</head>
<body>
  <section class="card card--front" aria-label="Card front">
    <div class="brand"><span class="brand__square"></span>Verodex</div>
  </section>

  <section class="card card--back" aria-label="Card back">
    <div class="brand"><span class="brand__square"></span>Verodex</div>
    <div class="divider"></div>
    <div class="contact">
      <p class="contact__name">Mara Kovelin</p>
      <p class="contact__title">Managing Director</p>
      <ul class="contact__list">
        <li class="contact__item">
          <svg viewBox="0 0 16 16"><path fill="#4a7fcb" d="M3 1.5l3 .5 1 3-2 1.5a9 9 0 004.5 4.5L11 9l3 1 .5 3-2 1.5C7 14 2 9 1.5 3.5z"/></svg>
          (555) 014-2290
        </li>
        <li class="contact__item">
          <svg viewBox="0 0 16 16"><rect x="1" y="3" width="14" height="10" rx="1" fill="#6f9fd8"/><path d="M1.5 3.5L8 9l6.5-5.5" fill="none" stroke="#fff" stroke-width="1.3"/></svg>
          info@verodex.com
        </li>
        <li class="contact__item">
          <svg viewBox="0 0 16 16"><circle cx="8" cy="8" r="7" fill="#4a7fcb"/><path d="M4 5c2 0 2 2 4 2s1 3 3 3M6 12c0-2 2-2 2-4" fill="none" stroke="#fff" stroke-width="1.2"/></svg>
          www.verodex.com
        </li>
      </ul>
    </div>
    <div class="address-band">
      <p class="address-band__stripe">418 Linden Ridge Rd. Suite 300 Riverton, TX 75010</p>
      <span class="address-band__tab"></span>
    </div>
  </section>
</body>
</html>
```